Im open to ideas.. I was thinking on my business cards aswell as my logo. a place for my name. email. phone number and abn..

ive attched a file with my business logo. which i dont love the colours.. i was think a dark background with charcoal letters so something along those colour schumes but im open to ideas..

BRM Constructions

```html
<!DOCTYPE html>
<html lang="en">
<head>
<meta charset="utf-8">
<title>BRM Constructions – Business Cards</title>
<link rel="stylesheet" href="https://fonts.googleapis.com/css2?family=Arimo:wght@400;700&display=swap">
<style>
  :root {
    --backdrop: #3b3330;
    --card: #1b1b1d;
    --card-edge: #2a2a2d;
    --charcoal: #3e3e42;
    --charcoal-light: #55555a;
    --white: #f2f2f2;
    --muted: #c9c9c9;
    --accent: #e0161d;
    --divider: #6a6a6e;
  }
  * { box-sizing: border-box; margin: 0; padding: 0; }
  html, body {
    width: 1200px;
    height: 787px;
    overflow: hidden;
    background: var(--backdrop);
    font-family: "Arimo", Arial, sans-serif;
  }
  .sheet {
    position: relative;
    width: 1200px;
    height: 787px;
    display: flex;
    align-items: center;
    justify-content: center;
    gap: 60px;
  }
  .card {
    position: relative;
    width: 520px;
    height: 298px;
    background: var(--card);
    border: 1px solid var(--card-edge);
    border-radius: 4px;
    box-shadow: 0 10px 26px rgba(0,0,0,.45);
  }

  /* Back of card: tonal wordmark */
  .card--back {
    display: flex;
    flex-direction: column;
    align-items: center;
    justify-content: center;
    gap: 34px;
  }
  .wordmark {
    display: flex;
    align-items: center;
    gap: 14px;
    font-weight: 700;
    line-height: 1;
  }
  .wordmark__mark { width: 18px; height: 18px; flex: none; }
  .wordmark__name { display: block; }
  .wordmark--tonal { color: var(--charcoal-light); font-size: 44px; letter-spacing: 1px; }
  .wordmark--tonal .wordmark__mark { background: var(--charcoal-light); width: 26px; height: 26px; }
  .website {
    color: var(--muted);
    font-size: 14px;
    letter-spacing: 4px;
  }

  /* Front of card: logo + contact details */
  .card--front {
    display: flex;
    align-items: center;
    padding: 0 30px 0 40px;
  }
  .card--front .wordmark {
    color: var(--white);
    font-size: 30px;
    flex: 1;
  }
  .card--front .wordmark__mark { background: var(--accent); }
  .rule {
    width: 1px;
    height: 170px;
    background: var(--divider);
    margin: 0 22px 0 18px;
  }
  .contact { width: 170px; color: var(--muted); font-size: 14px; }
  .contact__name { color: var(--accent); font-size: 19px; font-weight: 700; }
  .contact__role { color: var(--white); font-size: 16px; margin: 2px 0 14px; }
  .contact__row { display: flex; align-items: center; gap: 8px; margin-top: 8px; }
  .contact__icon { width: 14px; height: 14px; flex: none; fill: var(--accent); }
  .contact__abn { margin-bottom: 4px; }
</style>
</head>
<body>
<main class="sheet">
  <section class="card card--back" aria-label="Card back">
    <div class="wordmark wordmark--tonal">
      <span class="wordmark__mark"></span>
      <span class="wordmark__name">BRM Constructions</span>
    </div>
    <p class="website">www.brmbuild.com</p>
  </section>

  <section class="card card--front" aria-label="Card front">
    <div class="wordmark">
      <span class="wordmark__mark"></span>
      <span class="wordmark__name">BRM Constructions</span>
    </div>
    <div class="rule"></div>
    <div class="contact">
      <p class="contact__name">Sam Reeve</p>
      <p class="contact__role">President</p>
      <p class="contact__abn">ABN: 987654321</p>
      <p class="contact__row">
        <svg class="contact__icon" viewBox="0 0 24 24" aria-hidden="true"><path d="M6.6 10.8a15.1 15.1 0 0 0 6.6 6.6l2.2-2.2c.3-.3.7-.4 1-.2 1.1.4 2.3.6 3.6.6.6 0 1 .4 1 1V20c0 .6-.4 1-1 1A17 17 0 0 1 3 4c0-.6.4-1 1-1h3.5c.6 0 1 .4 1 1 0 1.3.2 2.5.6 3.6.1.3 0 .7-.2 1z"/></svg>
        <span>555 0142 7788</span>
      </p>
      <p class="contact__row">
        <svg class="contact__icon" viewBox="0 0 24 24" aria-hidden="true"><path d="M2 5h20v14H2z M3.5 6.5 12 13l8.5-6.5" fill="var(--accent)"/><path d="M3.5 6.5 12 13l8.5-6.5" fill="none" stroke="var(--card)" stroke-width="1.6"/></svg>
        <span>sam@brmbuild.com</span>
      </p>
    </div>
  </section>
</main>
</body>
</html>
```